Business Card Design for Software Development Company

I am looking for a business card design the incorporates my new logo (attached below).

Key information to include:
Name: Martin Quelbrook
Title: CEO
Email: martin@brightwellcivic.example
Phone: 555-218-9403
Website: www.brightwellcivic.example

NOTE: This design should be easy to edit so that we can order cards for different members of our team.

```html
<!DOCTYPE html>
<html lang="en">
<head>
<meta charset="utf-8">
<title>Brightwell Civic – Business Card</title>
<link rel="stylesheet" href="https://fonts.googleapis.com/css2?family=Montserrat:wght@400;600;700&display=swap">
<style>
  :root {
    --bg: #1c1c1c;
    --card: #262626;
    --teal: #14b19e;
    --orange: #e8832a;
    --text: #e9e9e9;
    --white: #f5f5f5;
  }
  * { margin: 0; padding: 0; box-sizing: border-box; }
  html, body {
    width: 1200px; height: 1059px; overflow: hidden;
    background: var(--bg);
    font-family: "Montserrat", sans-serif;
  }
  .canvas { position: relative; width: 1200px; height: 1059px; }
  .card {
    position: absolute;
    width: 690px; height: 392px;
    border-radius: 18px;
    background: var(--card);
  }
  .card--front { left: 256px; top: 89px; }
  .card--back { left: 255px; top: 546px; }

  /* Front */
  .brand-lockup {
    position: absolute; left: 62px; top: 176px;
    display: flex; align-items: center; gap: 10px;
  }
  .brand-square { width: 18px; height: 18px; background: var(--orange); }
  .brand-name {
    font-weight: 700; font-size: 32px; color: var(--teal);
    letter-spacing: 0.5px; line-height: 1;
  }
  .contact-block { position: absolute; left: 358px; top: 122px; color: var(--text); }
  .person-name {
    font-weight: 600; font-size: 22.5px; letter-spacing: 1.2px;
    line-height: 1; text-transform: uppercase;
  }
  .person-name .first { color: var(--teal); }
  .person-name .last { color: var(--orange); }
  .person-title { font-size: 15px; margin-top: 5px; letter-spacing: 0.5px; }
  .divider { width: 12px; height: 1px; background: var(--orange); margin: 19px 0 18px; }
  .contact-list { list-style: none; }
  .contact-list li {
    display: flex; align-items: center; gap: 8px;
    font-size: 16px; letter-spacing: 0.4px; height: 28px;
  }
  .contact-list svg { width: 11px; height: 11px; flex: none; fill: var(--orange); }

  /* Back */
  .wordmark {
    position: absolute; left: 0; right: 0; top: 158px;
    display: flex; justify-content: center;
  }
  .wordmark-inner { display: flex; flex-direction: column; align-items: flex-end; }
  .wordmark-row { display: flex; align-items: center; gap: 14px; }
  .wordmark-square { width: 26px; height: 26px; background: var(--orange); }
  .wordmark-name {
    font-weight: 700; font-size: 60px; color: var(--white);
    letter-spacing: -1px; line-height: 1;
  }
  .wordmark-tagline {
    font-weight: 700; font-size: 8px; color: var(--white);
    letter-spacing: 0.4px; margin-top: 4px;
  }
</style>
</head>
<body>
<main class="canvas">
  <section class="card card--front">
    <div class="brand-lockup">
      <span class="brand-square"></span>
      <span class="brand-name">Brightwell</span>
    </div>
    <div class="contact-block">
      <h1 class="person-name"><span class="first">Martin</span> <span class="last">Quelbrook</span></h1>
      <p class="person-title">CEO</p>
      <div class="divider"></div>
      <ul class="contact-list">
        <li>
          <svg viewBox="0 0 12 12" aria-hidden="true"><path d="M1 4c0-2 2-3 5-3s5 1 5 3v1H8.5V3.8H3.5V5H1z"/><rect x="2" y="6" width="8" height="5" rx="1"/></svg>
          555-218-9403
        </li>
        <li>
          <svg viewBox="0 0 12 12" aria-hidden="true"><path d="M1 5l5-4 5 4v6H1z"/><path d="M1 5l5 3.5L11 5" fill="none" stroke="#262626" stroke-width="1"/></svg>
          martin@brightwellcivic.example
        </li>
        <li>
          <svg viewBox="0 0 12 12" aria-hidden="true"><circle cx="6" cy="6" r="5.5"/><path d="M4 2.5c1 1 2 1.5 1 3s1.5 1.5 2 3M8 2c0 1 1 1.5 2 1.5" fill="none" stroke="#262626" stroke-width="1"/></svg>
          www.brightwellcivic.example
        </li>
      </ul>
    </div>
  </section>

  <section class="card card--back">
    <div class="wordmark">
      <div class="wordmark-inner">
        <div class="wordmark-row">
          <span class="wordmark-square"></span>
          <span class="wordmark-name">Brightwell Labs</span>
        </div>
        <span class="wordmark-tagline">A DIVISION OF BRIGHTWELL CIVIC</span>
      </div>
    </div>
  </section>
</main>
</body>
</html>
```